Need Business Card for our Real Estate Business with Sales Executive's Picture

PANTONE 484 C ( RED)

PANTONE 2766 C ( BLUE

Industry/Entity Type

Real Estate

Contact Information for Business Card

Name, Mobile, email, & picture of Person
Agency Phone, address, Web address

Requirements
Must have
• Our Logo Colours, Agent Picture,

```html
<!DOCTYPE html>
<html lang="en">
<head>
<meta charset="utf-8">
<title>Dunmore Realty – Business Card</title>
<link rel="stylesheet" href="https://fonts.googleapis.com/css2?family=Marcellus&family=Open+Sans:wght@400;600;700&display=swap">
<style>
  :root {
    --navy: #1a2a5e;
    --red: #a12a24;
    --white: #ffffff;
    --paper: #e4e4e6;
    --brand-font: "Marcellus", Georgia, serif;
    --body-font: "Open Sans", Arial, sans-serif;
  }
  * { box-sizing: border-box; margin: 0; padding: 0; }
  html, body { width: 1200px; height: 852px; overflow: hidden; }
  body { background: var(--paper); position: relative; font-family: var(--body-font); }

  .card {
    position: absolute;
    width: 500px; height: 290px;
    border-radius: 22px;
    overflow: hidden;
    box-shadow: 0 6px 14px rgba(0,0,0,.18);
  }

  /* Front */
  .card-front { left: 70px; top: 281px; background: var(--navy); color: var(--white); }
  .front-brand {
    position: absolute; left: 0; right: 0; top: 100px;
    display: flex; align-items: center; justify-content: center; gap: 12px;
  }
  .brand-square { width: 12px; height: 12px; background: var(--red); flex: none; }
  .front-brand .brand-name { font-family: var(--brand-font); font-size: 44px; letter-spacing: 3px; color: var(--white); }
  .front-rule { position: absolute; left: 120px; right: 120px; top: 168px; height: 1px; background: var(--white); opacity: .8; }
  .front-web {
    position: absolute; left: 0; right: 0; top: 214px; text-align: center;
    font-size: 13px; letter-spacing: .4px; color: var(--white);
  }
  .front-accent { position: absolute; top: 224px; height: 2px; width: 50px; background: var(--red); }
  .front-accent.left { left: 86px; }
  .front-accent.right { right: 86px; }

  /* Back */
  .card-back { left: 630px; top: 281px; background: var(--white); }
  .back-shapes { position: absolute; inset: 0; }
  .back-brand {
    position: absolute; left: 26px; top: 70px;
    display: flex; align-items: center; gap: 8px;
  }
  .back-brand .brand-name { font-family: var(--brand-font); font-size: 26px; letter-spacing: 2px; color: var(--navy); }
  .holder { position: absolute; right: 40px; top: 20px; text-align: right; }
  .holder-name { font-weight: 700; font-size: 17px; line-height: 22px; color: var(--navy); }
  .holder-title { font-size: 12px; line-height: 16px; color: var(--red); }
  .agent-photo {
    position: absolute; left: 90px; top: 150px; width: 160px; height: 140px;
    background: linear-gradient(180deg, #c9b7a6 0%, #8a6c58 45%, #2c3f7a 75%, #1d2b5c 100%);
    border-radius: 40px 40px 0 0;
  }
  .contact-list { position: absolute; right: 22px; top: 142px; list-style: none; text-align: right; }
  .contact-list li {
    display: flex; justify-content: flex-end; align-items: center; gap: 8px;
    color: var(--white); font-size: 11px; line-height: 19px; white-space: nowrap;
  }
  .contact-list .icon { width: 11px; height: 11px; flex: none; }
  .contact-list .spacer { width: 11px; flex: none; }
  .edge-dot { position: absolute; right: -10px; top: 22px; width: 20px; height: 20px; border-radius: 50%; background: var(--red); }
</style>
</head>
<body>

  <section class="card card-front" aria-label="Card front">
    <div class="front-brand">
      <span class="brand-square"></span>
      <span class="brand-name">Dunmore Realty</span>
    </div>
    <div class="front-rule"></div>
    <span class="front-accent left"></span>
    <p class="front-web">www.dunmorerealty.com</p>
    <span class="front-accent right"></span>
  </section>

  <section class="card card-back" aria-label="Card back">
    <svg class="back-shapes" viewBox="0 0 500 290" width="500" height="290" aria-hidden="true">
      <path d="M500,88 C380,92 300,108 262,158 C228,204 200,230 140,240 L0,246 L0,290 L500,290 Z" fill="var(--red)"/>
      <path d="M500,76 C374,80 290,98 250,150 C216,196 190,220 130,230 L0,236" fill="none" stroke="var(--navy)" stroke-width="7"/>
      <path d="M500,64 C366,70 280,88 240,142 C206,186 180,208 120,218" fill="none" stroke="var(--navy)" stroke-width="2.5"/>
    </svg>
    <span class="edge-dot"></span>

    <div class="back-brand">
      <span class="brand-square"></span>
      <span class="brand-name">Dunmore Realty</span>
    </div>

    <div class="holder">
      <p class="holder-name">Laura Whitfield</p>
      <p class="holder-title">Managing Director</p>
    </div>

    <div class="agent-photo" role="img" aria-label="Portrait photo of the agent in a navy suit"></div>

    <ul class="contact-list">
      <li>555.201.3370
        <svg class="icon" viewBox="0 0 12 12"><path d="M3 1 L5 3.5 L4 5 Q5.5 7 7 8 L8.5 7 L11 9 L9.5 11 Q4 10 1 2.5 Z" fill="var(--white)"/></svg>
      </li>
      <li>555-864-0419
        <svg class="icon" viewBox="0 0 12 12"><rect x="1" y="5" width="10" height="6" rx="1" fill="var(--white)"/><path d="M1 4 Q6 0 11 4" fill="none" stroke="var(--white)" stroke-width="1.6"/></svg>
      </li>
      <li>dunmorerealty.com
        <svg class="icon" viewBox="0 0 12 12"><rect x="1" y="2.5" width="10" height="7" fill="var(--white)"/><path d="M1 2.5 L6 6.5 L11 2.5" fill="none" stroke="var(--red)" stroke-width="1"/></svg>
      </li>
      <li>lwhitfield@dunmorerealty.com
        <svg class="icon" viewBox="0 0 12 12"><circle cx="6" cy="6" r="5" fill="none" stroke="var(--white)" stroke-width="1.2"/><path d="M1 6 H11 M6 1 Q3 6 6 11 Q9 6 6 1" fill="none" stroke="var(--white)" stroke-width="1"/></svg>
      </li>
      <li>48 Harbor Lane #210, Fairview, OR 97024<span class="spacer"></span></li>
    </ul>
  </section>

</body>
</html>
```